Anzeigengestaltung für eine Hausarztpraxis
Zielgruppe
Wir sind eine Hausarztpraxis mit zwei Standorten und suchen eine Ärztin oder einen Arzt zur Anstellung in der klassischen Hausarzt Medizin am Standort Lindmatt
Aufgabenstellung
Bitte beachtet den Text im Anhang, der ist schon vorgegeben. (Anzeigentext)
Wir suchen ein ruhiges, hochwertiges Layout für eine Stellenanzeige einer Hausarztpraxis in einem historischen Gebäude.
Der Text steht im Vordergrund, das Design soll zurückhaltend, klar und wertig sein.
Bitte keine Icons, keine bunten Farben, keine verspielten Elemente.
Gerne viel Weissraum, klare Typografie, ruhige Anmutung.
Schrift: Garamond für den Fliesstext (bereits gewählt).
Das Layout soll sowohl als PDF wie auch online funktionieren.
Optional: ein sehr dezentes grafisches Element oder eine ruhige Bildanmutung (z. B. Struktur, Licht, Architekturdetail).

```html
<!DOCTYPE html>
<html lang="de">
<head>
<meta charset="utf-8">
<title>Stellenanzeige Hausarztpraxis</title>
<link href="https://fonts.googleapis.com/css2?family=EB+Garamond:ital,wght@0,400;0,600;1,400&family=Manrope:wght@600;800&family=Open+Sans:ital,wght@1,400&display=swap" rel="stylesheet">
<style>
  :root {
    --stage: #ececec;
    --paper: #ffffff;
    --slate: #566a80;
    --slate-dark: #4a5d73;
    --slate-light: #6a7f96;
    --heading: #4d6580;
    --ink: #222428;
    --on-dark: #ffffff;
  }
  * { box-sizing: border-box; margin: 0; padding: 0; }
  html, body {
    width: 1200px; height: 800px; overflow: hidden;
    background: var(--stage);
  }
  .flyer {
    position: absolute; left: 330px; top: 18px;
    width: 540px; height: 764px;
    background: var(--paper);
    box-shadow: 0 6px 24px rgba(0,0,0,.12);
    overflow: hidden;
    display: flex; flex-direction: column;
  }
  .masthead {
    position: relative;
    flex: 0 0 258px;
    background: linear-gradient(100deg, var(--slate-light) 0%, var(--slate) 45%, var(--slate-dark) 100%);
    padding: 42px 60px 0 60px;
    color: var(--on-dark);
  }
  .masthead__texture {
    position: absolute; right: 30px; top: 64px;
    width: 190px; height: 194px;
    background: linear-gradient(160deg, rgba(255,255,255,.10), rgba(255,255,255,.02) 70%);
  }
  .brand {
    position: relative;
    display: flex; align-items: center; gap: 8px;
    font-family: "Manrope", sans-serif; font-weight: 600;
    font-size: 13px; color: var(--on-dark);
  }
  .brand__dot { width: 8px; height: 8px; border-radius: 50%; background: var(--on-dark); }
  .headline {
    position: relative;
    margin-top: 40px;
    font-family: "Manrope", sans-serif; font-weight: 800;
    font-size: 24px; line-height: 1.2; letter-spacing: .2px;
    max-width: 380px;
  }
  .tagline {
    position: relative;
    margin-top: 12px;
    font-family: "Open Sans", sans-serif; font-style: italic;
    font-size: 11.5px; letter-spacing: .3px;
  }
  .content {
    flex: 1;
    padding: 26px 60px 0 60px;
    font-family: "EB Garamond", serif;
    font-size: 10.8px; line-height: 1.42; color: var(--ink);
  }
  .content p + p { margin-top: 4px; }
  .section-title {
    margin-top: 11px; margin-bottom: 3px;
    font-family: "EB Garamond", serif; font-weight: 600;
    font-size: 13px; color: var(--heading);
  }
  .contact {
    display: flex; align-items: center;
    margin-top: 24px;
  }
  .contact__invite { width: 255px; }
  .contact__divider { width: 1px; height: 70px; background: var(--heading); margin: 0 28px; }
  .contact__address { font-size: 11.5px; line-height: 1.4; font-style: normal; }
  .label { color: var(--heading); font-weight: 600; }
  .strong { font-weight: 600; }
  .footer-band { flex: 0 0 30px; background: var(--slate); }
</style>
</head>
<body>
  <article class="flyer">
    <header class="masthead">
      <div class="masthead__texture" role="img" aria-label="Dezente Architekturstruktur aus gestapelten Blöcken"></div>
      <div class="brand"><span>Arztpraxis Lindenhof</span><span class="brand__dot"></span></div>
      <h1 class="headline">Hausarztmedizin mit Tiefe – dort, wo man noch echte Grundversorgung lebt</h1>
      <p class="tagline">Ein Ort, der trägt. Ein Team, das bleibt. Eine Arbeit, die Wertschätzung hat.</p>
    </header>

    <main class="content">
      <p>Manche Orte verändern die Art, wie man arbeitet. Unsere Praxis in Lindmatt ist so ein Ort. In einem historischen Gebäude gelegen, mit grosszügigem Ambiente, warmen Vertäfelungen und kunstvoller Wandbemalung, entstehen hier Behandlungsräume von Ruhe und Würde. Kein steriler Praxisalltag, sondern ein Ort, der Gespräche trägt und medizinische Arbeit unterstützt.</p>
      <p>Für diesen besonderen Ort suchen wir eine Hausärztin oder einen Hausarzt, die oder der nicht einfach einen Arbeitsplatz sucht, sondern einen Platz, an dem Medizin menschlich sein darf.</p>

      <h2 class="section-title">Ein Team mit Haltung</h2>
      <p>Sie arbeiten in einem freundlichen, über Jahre gewachsenen Team mit hoher personeller Kontinuität und geringer Fluktuation.</p>

      <h2 class="section-title">Zeit für gute Medizin</h2>
      <p>Unsere Patientinnen und Patienten sind überwiegend gut bis sehr gut situiert, wertschätzend und therapieoffen. Das ermöglicht ruhiges, strukturiertes Arbeiten mit Fokus auf Qualität, Beziehung und nachhaltige Behandlung.</p>

      <h2 class="section-title">Und sonst?</h2>
      <p>Der Praxisalltag ist klar strukturiert, ruhig und verlässlich. Geregelte und in Abstimmung flexible Arbeitszeiten ohne Wochenend- oder Nachtdienste, eine sehr gute leistungsbezogene Vergütung sowie ein respektvoller, wertschätzender Umgang auf Augenhöhe schaffen ein Umfeld, in dem man sich auf die medizinische Arbeit konzentrieren und langfristig wohlfühlen kann.</p>

      <section class="contact">
        <div class="contact__invite">
          <p>Wir freuen uns über eine unkomplizierte Kontaktaufnahme per <span class="strong">E-Mail oder Telefon</span> – gerne auch ganz unverbindlich und ohne vollständige Bewerbungsunterlagen.</p>
          <p><span class="label">E-Mail:</span> Helga.Weißmoor@arztpraxis-lindenhof.ch</p>
        </div>
        <div class="contact__divider"></div>
        <address class="contact__address">
          <span class="label">Arztpraxis Lindenhof</span><br>
          Lindenweg 5<br>
          4718 Lindmatt<br>
          <span class="label">Tel:</span> 0621834705
        </address>
      </section>
    </main>

    <footer class="footer-band"></footer>
  </article>
</body>
</html>
```